Business Card Design

I already have a company logo for my company. I have a logo for the manufacturer we represent. I want a professional business card design.

```html
<!DOCTYPE html>
<html lang="en">
<head>
<meta charset="UTF-8">
<title>Signal Guard LLC — Business Card</title>
<link href="https://fonts.googleapis.com/css2?family=Open+Sans:wght@400;600;700&display=swap" rel="stylesheet">
<style>
  :root {
    --backdrop: #1f1f20;
    --card: #232326;
    --ink: #f2f2f2;
    --red: #e42127;
    --gold: #d9a21f;
    --rule: #8a8a8e;
  }
  * { box-sizing: border-box; margin: 0; padding: 0; }
  html, body {
    width: 1200px; height: 780px; overflow: hidden;
    background: var(--backdrop);
    font-family: "Open Sans", Arial, sans-serif;
  }
  .canvas { position: relative; width: 1200px; height: 780px; }

  .card {
    position: absolute; top: 241px;
    width: 520px; height: 298px;
    background: var(--card);
    border-radius: 3px;
    box-shadow: 0 14px 30px rgba(0,0,0,.55);
    overflow: hidden;
  }
  .card--front { left: 50px; }
  .card--back { left: 630px; }

  .brand {
    display: flex; align-items: center; gap: 10px;
    color: var(--ink); font-weight: 700; letter-spacing: .5px;
    text-transform: uppercase; white-space: nowrap;
  }
  .brand__mark { width: 14px; height: 14px; background: var(--red); flex: none; }

  .card--front .brand { position: absolute; left: 34px; top: 76px; font-size: 18px; }

  .divider { position: absolute; left: 0; top: 0; width: 520px; height: 298px; }

  .address {
    position: absolute; left: 34px; bottom: 34px;
    color: var(--ink); font-size: 12.5px; line-height: 1.4; white-space: nowrap;
  }

  .contact { position: absolute; left: 322px; top: 64px; }
  .person__name { font-size: 26px; font-weight: 600; line-height: 1.1; white-space: nowrap; }
  .person__first { color: var(--red); }
  .person__last { color: var(--gold); }
  .person__title { color: var(--ink); font-size: 13.5px; margin-top: 4px; }

  .details { list-style: none; margin-top: 20px; }
  .details li {
    display: flex; align-items: center; gap: 10px;
    color: var(--ink); font-size: 13px; line-height: 1; margin-bottom: 10px; white-space: nowrap;
  }
  .details svg { width: 14px; height: 14px; flex: none; }

  .card--back { display: flex; align-items: center; justify-content: center; }
  .card--back .brand { font-size: 30px; gap: 14px; }
  .card--back .brand__mark { width: 20px; height: 20px; }
</style>
</head>
<body>
<main class="canvas">

  <section class="card card--front" aria-label="Business card front">
    <div class="brand"><span class="brand__mark"></span>Signal Guard LLC</div>

    <svg class="divider" viewBox="0 0 520 298" aria-hidden="true">
      <line x1="302" y1="44" x2="270" y2="206" stroke="var(--rule)" stroke-width="0.8"/>
    </svg>

    <p class="address">1840 Meadow Ridge Ln. Suite 300 Dallas, TX 75201</p>

    <div class="contact">
      <h1 class="person__name"><span class="person__first">Daniel</span> <span class="person__last">Kovar</span></h1>
      <p class="person__title">Managing Director</p>
      <ul class="details">
        <li>
          <svg viewBox="0 0 16 16" aria-hidden="true"><path fill="var(--red)" d="M3.6 1.5l2.3 2.6-1.3 1.6c.9 2 2.6 3.7 4.6 4.6l1.6-1.3 2.6 2.3-1.2 2.1C7.2 13.3 2.7 8.8 1.5 3l2.1-1.5z"/></svg>
          (555) 014-2738
        </li>
        <li>
          <svg viewBox="0 0 16 16" aria-hidden="true"><rect x="1.5" y="3.5" width="13" height="9" rx="1" fill="var(--red)"/><path d="M2 4.5l6 4.5 6-4.5" fill="none" stroke="var(--card)" stroke-width="1.2"/></svg>
          hello@signalguard.com
        </li>
        <li>
          <svg viewBox="0 0 16 16" aria-hidden="true"><circle cx="8" cy="8" r="6.5" fill="var(--red)"/><path d="M1.5 8h13M8 1.5c-3 3.5-3 9.5 0 13M8 1.5c3 3.5 3 9.5 0 13" fill="none" stroke="var(--card)" stroke-width="1"/></svg>
          www.signalguard.com
        </li>
      </ul>
    </div>
  </section>

  <section class="card card--back" aria-label="Business card back">
    <div class="brand"><span class="brand__mark"></span>Signal Guard LLC</div>
  </section>

</main>
</body>
</html>
```